Stylish Business Cards Wanted

- DOUBLE SIDED Design Required -

High end, edgy cards for a corporate and personal stylist. Must include logo,
Name: Belinda Harwick
Title: Director and Stylist
telephone : +61 8 7142 5809
email: belinda@theloombriefing.example
website: theloombriefing.example
Tag: Corporate Workwear & Uniform Specialist | Personal Stylist
Would like nice icons for telephone, email, website

Target Market(s)

Businesses wanting stylish uniforms, people wanting stylish wardrobes

Industry/Entity Type

Corporate Workwear Stylist

Contact Information for Business Card

I would like black, white and gold foiling incorporated in the design - possibly a touch of the other colours on my branding guide attached Name: Belinda Harwick Title: Director and Stylist telephone : +61 8 7142 5809 email: belinda@theloombriefing.example website: theloombriefing.example Tag: Corporate Workwear & Uniform Specialist | Personal Stylist Would like nice icons for telephone, email, website

Font styles to use
Other font styles liked:
• Raleway

Colors

Designer to choose colors to be used in the design.

Requirements
Must have
• Gold foil accents

```html
<!DOCTYPE html>
<html lang="en">
<head>
<meta charset="utf-8">
<title>The Loom Briefing – Business Cards</title>
<link rel="stylesheet" href="https://fonts.googleapis.com/css2?family=Dancing+Script:wght@600&family=Raleway:wght@600&family=Roboto:wght@400&display=swap">
<style>
  :root {
    --backdrop: #d9d9d9;
    --navy: #141b2e;
    --gold: #d2a63c;
    --paper: #fbfbfa;
    --ink: #1f2433;
    --accent-pink: #e0307a;
  }
  * { box-sizing: border-box; margin: 0; padding: 0; }
  html, body {
    width: 1200px; height: 852px; overflow: hidden;
    background: var(--backdrop);
  }
  .sheet {
    position: relative; width: 1200px; height: 852px;
    display: flex; align-items: center; justify-content: center; gap: 60px;
  }
  .card {
    position: relative; width: 510px; height: 296px;
    border-radius: 22px; overflow: hidden;
  }
  .card--front {
    background: var(--navy);
    display: flex; align-items: center; justify-content: center;
  }
  .brand-name {
    font-family: "Raleway", sans-serif; font-weight: 600;
    letter-spacing: 0.04em;
  }
  .card--front .brand-name { color: var(--gold); font-size: 40px; }
  .card--back { background: var(--paper); }
  .card--back .brand-name {
    position: absolute; top: 44px; right: 34px;
    color: var(--navy); font-size: 24px;
  }
  .divider { position: absolute; inset: 0; width: 100%; height: 100%; }
  .services {
    position: absolute; right: 30px; top: 118px;
    font-family: "Roboto", sans-serif; font-size: 13.5px; line-height: 1.45;
    color: var(--ink); text-align: right; list-style: none;
  }
  .services .chevron { color: var(--accent-pink); margin-left: 4px; font-size: 11px; }
  .person { position: absolute; left: 32px; top: 152px; }
  .person__name {
    font-family: "Dancing Script", cursive; font-weight: 600;
    font-size: 30px; color: var(--gold); line-height: 1;
  }
  .person__title {
    font-family: "Roboto", sans-serif; font-size: 13px; color: var(--ink);
    margin-top: 6px;
  }
  .person__rule {
    width: 200px; height: 1px; background: var(--gold); margin-top: 10px;
  }
  .contacts {
    position: absolute; left: 32px; top: 226px; list-style: none;
    font-family: "Roboto", sans-serif; font-size: 13px; color: var(--ink);
  }
  .contacts li { display: flex; align-items: center; gap: 10px; height: 20px; }
  .contacts svg { width: 13px; height: 13px; flex: none; }
</style>
</head>
<body>
<main class="sheet">
  <section class="card card--front" aria-label="Card front">
    <span class="brand-name">The Loom Briefing</span>
  </section>

  <section class="card card--back" aria-label="Card back">
    <span class="brand-name">The Loom Briefing</span>

    <svg class="divider" viewBox="0 0 510 296" aria-hidden="true">
      <path d="M510 92 H350 C330 92 322 112 300 112 H32" fill="none" stroke="var(--gold)" stroke-width="1"/>
    </svg>

    <ul class="services">
      <li>Personal Stylist<span class="chevron">«</span></li>
      <li>Corporate Workwear<span class="chevron">«</span></li>
      <li>&amp; Uniform Specialist<span class="chevron">«</span></li>
    </ul>

    <div class="person">
      <p class="person__name">Belinda Harwick</p>
      <p class="person__title">Director and Stylist</p>
      <div class="person__rule"></div>
    </div>

    <ul class="contacts">
      <li>
        <svg viewBox="0 0 16 16" fill="none" stroke="var(--gold)" stroke-width="1.3" aria-hidden="true">
          <circle cx="8" cy="8" r="7"/>
          <path d="M5.5 4.5l1.3 1.6-.8 1c.5 1.1 1.3 1.9 2.4 2.4l1-.8 1.6 1.3-.8 1.3C7.8 11 5 8.2 4.6 5.3z"/>
        </svg>
        +61 8 7142 5809
      </li>
      <li>
        <svg viewBox="0 0 16 16" fill="none" stroke="var(--gold)" stroke-width="1.3" aria-hidden="true">
          <rect x="1.5" y="3.5" width="13" height="9" rx="1"/>
          <path d="M1.5 4l6.5 5 6.5-5"/>
        </svg>
        belinda@theloombriefing.example
      </li>
      <li>
        <svg viewBox="0 0 16 16" fill="none" stroke="var(--gold)" stroke-width="1.3" aria-hidden="true">
          <circle cx="8" cy="8" r="6.5"/>
          <ellipse cx="8" cy="8" rx="2.8" ry="6.5"/>
          <path d="M1.5 8h13"/>
        </svg>
        www.theloombriefing.example
      </li>
    </ul>
  </section>
</main>
</body>
</html>
```